Wordpress theme website for professionals working together

My partner and I are offering business services, my wife in the energy business as mainly as member of the board of commissioners. I am working as interim manager/consultant in the accounting and finance area. Both activities are connected in one company VELMOT BV (dutch ltd). We need a CV based website. Beside this we do some financial and accounting services.

Target Market(s)

small medium business

Font styles to use
Sans Serif

Colors

Designer to choose colors to be used in the design.

Requirements
Must have
• Pictures of both members.
• CLEAN AND SIMPLE
• I LIKE BLACK & WHITE
Nice to have
• I like design like this theme: http://theme.pruxelo-example.com/resume/

```html
<!DOCTYPE html>
<html lang="en">
<head>
<meta charset="utf-8">
<title>VELMOT BV – Resume</title>
<link href="https://fonts.googleapis.com/css2?family=Mulish:wght@400;600;700;800&display=swap" rel="stylesheet">
<style>
:root{
  --ink:#1f1f1f;
  --text:#555;
  --muted:#777;
  --dark:#2a2a2b;
  --dark-2:#1e1e1f;
  --light:#f0f0f0;
  --line:#dcdcdc;
  --white:#fff;
}
*{box-sizing:border-box;margin:0;padding:0}
html,body{width:1200px;height:4091px;overflow:hidden}
body{position:relative;font-family:'Mulish',Arial,sans-serif;color:var(--text);background:var(--white)}
.abs{position:absolute}
/* header */
.site-header{position:absolute;left:0;top:0;width:1200px;height:128px;background:var(--white)}
.brand{position:absolute;left:115px;top:44px;font-size:36px;font-weight:800;color:var(--ink);letter-spacing:1px}
.main-nav{position:absolute;left:476px;top:54px;display:flex;gap:14px;font-size:15px;color:var(--ink)}
.nav-button{position:absolute;left:990px;top:46px;width:95px;height:36px;background:var(--ink);color:var(--white);font-size:14px;font-weight:700;display:flex;align-items:center;justify-content:center}
/* hero */
.hero{position:absolute;left:0;top:128px;width:1200px;height:518px;background:linear-gradient(90deg,#f4f4f4,#e2e2e2)}
.hero-photo{position:absolute;left:736px;top:0;width:464px;height:518px;background:linear-gradient(135deg,#d8d8d8,#8a8a8a 60%,#5a5a5a)}
.hero-title{position:absolute;left:112px;top:120px;font-size:82px;font-weight:800;color:var(--ink);letter-spacing:2px}
.hero-lead{position:absolute;left:112px;top:220px;font-size:20px;line-height:33px;color:var(--muted)}
.hero-signature{position:absolute;left:112px;top:335px;width:80px;height:30px;background:#d6d6d6;border-radius:4px}
/* section titles */
.section-title{position:absolute;left:0;width:1200px;text-align:center;font-size:29px;font-weight:600;color:var(--ink);letter-spacing:1px}
.section-sub{position:absolute;left:0;width:1200px;text-align:center;font-size:14px;line-height:27px;color:var(--text)}
/* personal card */
.info-card{position:absolute;left:145px;top:837px;width:886px;height:276px;background:var(--white);box-shadow:0 4px 18px rgba(0,0,0,.18)}
.card-heading{position:absolute;font-size:19px;font-weight:700;color:var(--ink)}
.story-text{position:absolute;left:72px;top:65px;width:385px;font-size:13.5px;line-height:29px;color:var(--muted)}
.btn-dark{position:absolute;background:var(--ink);color:var(--white);font-weight:700;font-size:15px;display:flex;align-items:center;justify-content:center}
.facts{position:absolute;left:538px;top:62px;font-size:14px;color:var(--ink)}
.facts div{display:flex;height:33px;align-items:center}
.facts span:first-child{width:80px;font-weight:700}
.social-dots{position:absolute;left:538px;top:233px;display:flex;gap:16px}
.social-dots i{width:9px;height:9px;border-radius:50%;background:var(--ink);display:block}
/* job */
.job{position:absolute;left:0;top:1203px;width:1200px;height:425px;background:linear-gradient(135deg,var(--dark),var(--dark-2))}
.job .section-title,.job .section-sub{color:var(--white)}
.job-col{position:absolute;top:196px;color:var(--white);font-size:14px;line-height:25px}
.job-col b{display:block;font-size:14px;letter-spacing:.5px;margin-top:54px}
.job-col svg{position:absolute;left:0;top:0}
/* skills */
.skills-title{position:absolute;left:112px;top:1704px;font-size:29px;font-weight:600;color:var(--ink)}
.skills-text{position:absolute;left:112px;width:430px;font-size:13px;line-height:26px;color:var(--muted)}
.skill{position:absolute;left:660px;width:360px}
.skill-label{font-size:12px;color:var(--ink);height:16px}
.skill-track{position:relative;height:8px;background:var(--line)}
.skill-fill{position:absolute;left:0;top:0;height:8px;background:var(--dark)}
.skill-tag{position:absolute;top:-14px;font-size:8px;font-weight:700;color:var(--white);background:#111;padding:1px 5px}
/* experience */
.experience-bg{position:absolute;left:0;top:2030px;width:1200px;height:1040px}
.timeline-line{position:absolute;left:616px;top:2290px;width:2px;height:540px;background:#999}
.exp-card{position:absolute;width:766px;height:145px;background:var(--white);box-shadow:0 2px 10px rgba(0,0,0,.06)}
.exp-body{position:absolute;top:20px;width:360px;font-size:13.5px;line-height:26px;color:var(--text)}
.exp-year{position:absolute;top:26px;font-size:24px;font-weight:700;color:var(--ink)}
.exp-role{position:absolute;top:64px;width:270px;font-size:15px;line-height:30px;font-weight:700;color:var(--ink)}
.exp-dot{position:absolute;left:603px;width:28px;height:28px;border-radius:50%;background:var(--ink);color:var(--white);font-size:12px;font-weight:700;display:flex;align-items:center;justify-content:center;border:3px solid var(--white)}
.right{text-align:right}
/* portfolio */
.portfolio-item{position:absolute;top:3182px;width:233px;height:238px}
.arrow{position:absolute;top:3292px}
/* band */
.work-band{position:absolute;left:0;top:3504px;width:1200px;height:259px;background:linear-gradient(135deg,var(--dark),var(--dark-2));color:var(--white);text-align:center}
.work-band h2{position:absolute;left:0;top:60px;width:1200px;font-size:29px;font-weight:600}
.work-band h3{position:absolute;left:0;top:103px;width:1200px;font-size:20px;font-weight:700}
.work-band p{position:absolute;left:0;top:142px;width:1200px;font-size:14px;line-height:27px}
/* footer */
.footer-brand{position:absolute;left:112px;top:3862px;font-size:29px;font-weight:800;color:var(--ink)}
.footer-col{position:absolute;top:3816px;font-size:14px;color:var(--ink)}
.footer-col h4{font-size:18px;font-weight:700;margin-bottom:10px}
.footer-col li{list-style:none;height:27px;display:flex;align-items:center;gap:8px}
.footer-col li i{width:10px;height:10px;border-radius:50%;background:var(--ink);display:block}
.news-input{position:absolute;left:799px;top:3853px;width:286px;height:44px;border:1.5px solid var(--ink);font-size:12px;color:var(--ink);padding-left:10px;display:flex;align-items:center}
.footer-rule{position:absolute;left:112px;top:4022px;width:973px;height:1px;background:var(--line)}
.copyright{position:absolute;left:0;top:4050px;width:1200px;text-align:center;font-size:13px;color:var(--ink)}
</style>
</head>
<body>

<header class="site-header">
  <div class="brand">VELMOT BV</div>
  <nav class="main-nav"><span>HOME</span><span>ABOUT ME</span><span>PORTFOLIO</span><span>TESTIMONIAL</span><span>CONTACT US</span></nav>
  <div class="nav-button">LOTTE</div>
</header>

<section class="hero">
  <div class="hero-photo" role="img" aria-label="Black and white portrait of Bram, advisor, wearing glasses"></div>
  <h1 class="hero-title">VELMOT</h1>
  <p class="hero-lead">Hi I'm Bram, Advisor KWD.<br>Sed ut perspiciatis unde omnis iste natus sit<br>voluptatem accusantium doloremque.</p>
  <div class="hero-signature" role="img" aria-label="Handwritten signature"></div>
</section>

<h2 class="section-title" style="top:710px">PERSONAL INFORMATION</h2>
<p class="section-sub" style="top:757px">Lorem ipsum dolor sit amet, consectetur adipiscing elit, sed do eiusmod tempor<br>incididunt utlabore dolore magna aliqua. Ut enim minim venil.</p>

<div class="info-card">
  <div class="card-heading" style="left:72px;top:24px">My Story</div>
  <p class="story-text">Sed ut perspiciatis unde omnis iste natus error sit volupt atem accusantium doloremque laudantium, totam rem aperiam, eaque ipsa quae ab illo inventore veritatis et quasi architecto beatae vitacta sunt explicabo.</p>
  <div class="btn-dark" style="left:74px;top:199px;width:115px;height:40px">Read More</div>
  <div class="card-heading" style="left:538px;top:24px">Personal Information</div>
  <div class="facts">
    <div><span>Name</span><span>Bram</span></div>
    <div><span>Age</span><span>52</span></div>
    <div><span>Phone</span><span>(+31) 555 010 0100</span></div>
    <div><span>Email</span><span>info@velmot-example.com</span></div>
    <div><span>Education</span><span>Vantrel (RA), Atheneum B.</span></div>
  </div>
  <div class="social-dots"><i></i><i></i><i></i><i></i></div>
</div>

<section class="job">
  <h2 class="section-title" style="top:52px">JOB</h2>
  <p class="section-sub" style="top:102px">Lorem ipsum dolor sit amet, consectetur adipiscing elit, sedo eiusmod tempor incididunt ut<br>labore dolore magna aliqua veniam, quis exercitation ullamco laboris.</p>
  <div class="job-col" style="left:330px">
    <svg width="52" height="50" viewBox="0 0 52 50" fill="none" stroke="#fff" stroke-width="2"><rect x="4" y="4" width="30" height="40"/><line x1="10" y1="14" x2="28" y2="14"/><line x1="10" y1="22" x2="28" y2="22"/><line x1="10" y1="30" x2="22" y2="30"/><path d="M46 10 L30 38 L28 44 L33 40 L49 12 Z"/></svg>
    <b>ACTUAL JOBS</b>Advisor KWD,<br>Advisor Hollow &amp; Knower pool
  </div>
  <div class="job-col" style="left:635px">
    <svg width="56" height="50" viewBox="0 0 56 50" fill="none" stroke="#fff" stroke-width="2"><circle cx="28" cy="9" r="7"/><path d="M24 9 l3 3 l5 -6"/><circle cx="12" cy="28" r="5"/><circle cx="28" cy="28" r="5"/><circle cx="44" cy="28" r="5"/><path d="M3 46 q9 -12 18 0 M19 46 q9 -12 18 0 M35 46 q9 -12 18 0"/></svg>
    <b>FINISHED JOBS</b>Controller a.i. KWD<br>Advisor Delta Field, Financial director
  </div>
</section>

<h2 class="skills-title">SKILLS</h2>
<p class="skills-text" style="top:1755px">At vero eos et accusamus et iusto odio dignissimos ducimus qui blanities ditis praesentium voluptatum deleniti atque corrupti quos dolores et quas molestias quidem rerum facilis est quaerat.</p>
<p class="skills-text" style="top:1857px">At vero eos et accusamus et iusto odio dignissimos ducimus qui blanit ditiis praesentium voluptatum deleniti atque corrupti quos dolores et quas molestias excepturi sint occaecati cupiditate non provident, simi ilique sunt in culpa qui officia deserunt mollitia animi voluntas.</p>

<div class="skill" style="top:1720px"><div class="skill-label">General Management</div><div class="skill-track"><div class="skill-fill" style="width:72%"></div><span class="skill-tag" style="left:62%">72%</span></div></div>
<div class="skill" style="top:1758px"><div class="skill-label">Energy knowledge</div><div class="skill-track"><div class="skill-fill" style="width:48%"></div><span class="skill-tag" style="left:38%">48%</span></div></div>
<div class="skill" style="top:1796px"><div class="skill-label">Gas knowledge</div><div class="skill-track"><div class="skill-fill" style="width:92%"></div><span class="skill-tag" style="left:82%">92%</span></div></div>
<div class="skill" style="top:1836px"><div class="skill-label">People management</div><div class="skill-track"><div class="skill-fill" style="width:50%"></div><span class="skill-tag" style="left:40%">50%</span></div></div>
<div class="skill" style="top:1878px"><div class="skill-label">Project management</div><div class="skill-track"><div class="skill-fill" style="width:51%"></div><span class="skill-tag" style="left:41%">51%</span></div></div>
<div class="skill" style="top:1916px"><div class="skill-label">Team player</div><div class="skill-track"><div class="skill-fill" style="width:75%"></div><span class="skill-tag" style="left:65%">75%</span></div></div>
<div class="skill" style="top:1955px"><div class="skill-label">Trouble shooter</div><div class="skill-track"><div class="skill-fill" style="width:76%"></div><span class="skill-tag" style="left:66%">76%</span></div></div>

<svg class="experience-bg" viewBox="0 0 1200 1040" preserveAspectRatio="none" aria-hidden="true">
  <path d="M0 40 Q600 -30 1200 60 L1200 980 Q600 1080 0 1010 Z" fill="#efefef"/>
</svg>
<h2 class="section-title" style="top:2180px">EXPERIENCE</h2>
<div class="timeline-line"></div>

<div class="exp-card" style="left:194px;top:2266px">
  <p class="exp-body right" style="left:30px">At vero eos et accusamus et iusto odio dignissimos ducimus qui blanditis praesentium voluptatum deleniti atque corrupti quos dolores et quas molestias excepturi sintat, officia deserunt mollitia animi, id estrum fuga.</p>
  <div class="exp-year" style="left:466px">2016-PRESENT</div>
  <div class="exp-role" style="left:466px">Quibusdam et aut officiis debitis aut rerum necessitatibus</div>
</div>
<div class="exp-card" style="left:284px;top:2438px">
  <div class="exp-year right" style="left:30px;width:290px">2013-2016</div>
  <div class="exp-role right" style="left:50px">Quibusdam et aut officiis debitis aut rerum necessitatibus</div>
  <p class="exp-body" style="left:376px">At vero eos et accusamus et iusto odio dignissimos ducimus qui blanditiis praesentium voluptatum deleniti atque corrupti quos dolores et quas molestias excepturi sintat, officia deserunt mollitia animi, id estrum fuga.</p>
</div>
<div class="exp-card" style="left:194px;top:2618px">
  <p class="exp-body right" style="left:30px">At vero eos et accusamus et iusto odio dignissimos ducimus qui blanditis praesentium voluptatum deleniti atque corrupti quos dolores et quas molestias excepturi sintat, officia deserunt mollitia animi, id estrum fuga.</p>
  <div class="exp-year" style="left:466px">2000-2013</div>
  <div class="exp-role" style="left:466px">Quibusdam et aut officiis debitis aut rerum necessitatibus</div>
</div>
<div class="exp-card" style="left:284px;top:2790px">
  <div class="exp-year right" style="left:30px;width:290px">1990-2000</div>
  <div class="exp-role right" style="left:50px">Quibusdam et aut officiis debitis aut rerum necessitatibus</div>
  <p class="exp-body" style="left:376px">At vero eos et accusamus et iusto odio dignissimos ducimus qui blanditiis praesentium voluptatum deleniti atque corrupti quos dolores et quas molestias excepturi sintat, officia deserunt mollitia animi, id estrum fuga.</p>
</div>
<div class="exp-dot" style="top:2285px">1</div>
<div class="exp-dot" style="top:2459px">2</div>
<div class="exp-dot" style="top:2637px">3</div>
<div class="exp-dot" style="top:2811px">4</div>

<h2 class="section-title" style="top:3115px">PORTFOLIO</h2>
<svg class="arrow" style="left:50px" width="16" height="20" viewBox="0 0 16 20"><path d="M11 3 L4 10 L11 17" fill="none" stroke="#1f1f1f" stroke-width="2.5"/></svg>
<div class="portfolio-item" style="left:112px;background:linear-gradient(135deg,#e9ecef,#7d8a96)" role="img" aria-label="Business documents with charts on a desk"></div>
<div class="portfolio-item" style="left:360px;background:linear-gradient(135deg,#f3ece6,#9c8a7c)" role="img" aria-label="Colleagues reviewing paperwork at a table"></div>
<div class="portfolio-item" style="left:608px;background:linear-gradient(135deg,#dfe3e8,#5b6470)" role="img" aria-label="Hands working on a tablet beside reports"></div>
<div class="portfolio-item" style="left:854px;background:linear-gradient(135deg,#f0eeea,#a59e94)" role="img" aria-label="Financial charts and a laptop on a desk"></div>
<svg class="arrow" style="left:1146px" width="16" height="20" viewBox="0 0 16 20"><path d="M5 3 L12 10 L5 17" fill="none" stroke="#1f1f1f" stroke-width="2.5"/></svg>

<section class="work-band">
  <h2>BRAM WORK</h2>
  <h3>Worked For - Harlow Advocaten &amp; Notarissen Brixton</h3>
  <p>Lorem ipsum dolor sit amet, consectetur adipiscing elit, sed do eiusmod tempor incididunt ut labore dolore<br>magna aliqua veniam, quis nostrud exercitation ullamco laboris.</p>
</section>

<footer>
  <div class="footer-brand">VELMOT BV</div>
  <div class="footer-col" style="left:325px">
    <h4>Quick links</h4>
    <ul><li>About Me</li><li>Experience</li><li>Skills</li><li>Portfolio</li><li>Contact</li></ul>
  </div>
  <div class="footer-col" style="left:562px">
    <h4>Social Link</h4>
    <ul><li><i></i>- Facepage</li><li><i></i>- Chirper</li><li><i></i>- Linkup</li><li><i></i>- Snapgram</li></ul>
  </div>
  <div class="footer-col" style="left:799px"><h4>Subscribe Newsletter</h4></div>
  <div class="news-input">Enter the Email</div>
  <div class="btn-dark" style="left:799px;top:3913px;width:115px;height:42px;font-size:13px">Subscribe</div>
  <div class="footer-rule"></div>
  <p class="copyright">Copyrights © 2018.All rights reserved</p>
</footer>

</body>
</html>
```